Consultancy Business Card Design

We need a business card design for a new company based in singapore called KestrelOak. KestrelOak a boutique consultancy firm offering broad-based business solutions, from conception to re-invention, for ventures from new start-ups to long-running traditional businesses.
Its 2 main divisions (Food & Beverage Operations and Construction & Project Management) have access to a wide range of networks, knowledge bases, and resources to service its clients across numerous diverse sectors. This includes, and is not limited to, construction, F&B, and retail.
We are a company that combines the ambition, boldness and energy of one in the 20s with the dedication, level-headedness and dependability of one entering its 30s. Bridging the experiences of the old with ideals of the young, we draw on the positives of both to create a unique synergy.
We hope to see designs that fits our company profile.
Industry/Entity Type
Boutique
Contact Information for Business Card
KestrelOak(Company Name)
Marcus Thiel (Name)
Principle Consultant (Title)
F&B and Hospitality (Division)
(+65) 8043 5617 (Contact no.)
marcus@kestreloak.com.sg (Email)
Colors
Designer to choose colors to be used in the design.

```html
<!DOCTYPE html>
<html lang="en">
<head>
<meta charset="utf-8">
<title>KestrelOak – Business Card</title>
<link href="https://fonts.googleapis.com/css2?family=Montserrat:wght@400;500;600&display=swap" rel="stylesheet">
<style>
  :root {
    --stage: #2a2a2b;
    --card: #1c1c1d;
    --card-glow: #2b2b2c;
    --accent: #e0262b;
    --text: #f2f2f2;
    --muted: #cfcfcf;
  }
  * { box-sizing: border-box; margin: 0; padding: 0; }
  html, body { width: 1200px; height: 900px; overflow: hidden; }
  body {
    background: var(--stage);
    font-family: "Montserrat", sans-serif;
    display: flex;
    align-items: center;
    justify-content: center;
    gap: 80px;
  }
  .card {
    position: relative;
    width: 360px;
    height: 620px;
    background: radial-gradient(ellipse at 55% 45%, var(--card-glow), var(--card) 70%);
    border-left: 7px solid var(--accent);
    box-shadow: 0 18px 40px rgba(0,0,0,.45);
  }
  .wordmark {
    position: absolute;
    left: 28px;
    top: 78px;
    font-size: 40px;
    font-weight: 500;
    color: var(--text);
    letter-spacing: 0.5px;
  }
  .card-back .wordmark { top: 110px; left: 40px; }
  .details {
    position: absolute;
    left: 0; right: 0;
    top: 250px;
    display: flex;
    flex-direction: column;
    align-items: center;
    text-align: center;
    color: var(--text);
  }
  .icon-box {
    width: 34px;
    height: 34px;
    border: 2px solid var(--accent);
    display: flex;
    align-items: center;
    justify-content: center;
    margin-bottom: 16px;
  }
  .icon-box svg { width: 18px; height: 18px; fill: var(--accent); }
  .block { margin-bottom: 56px; font-size: 14px; font-weight: 500; line-height: 1.45; }
  .block:last-child { margin-bottom: 0; }
  .role { color: var(--accent); }
  .accent { color: var(--accent); }
</style>
</head>
<body>

  <section class="card card-front">
    <div class="wordmark">KestrelOak</div>
    <div class="details">
      <div class="icon-box">
        <svg viewBox="0 0 20 20" aria-hidden="true"><circle cx="10" cy="6" r="4"/><path d="M2 18c0-4.5 3.6-7 8-7s8 2.5 8 7z"/></svg>
      </div>
      <div class="block contact-name">
        <div>Marcus Thiel</div>
        <div class="role">- Principle Consultant -</div>
        <div>F&amp;B and Hospitality</div>
      </div>

      <div class="icon-box">
        <svg viewBox="0 0 20 20" aria-hidden="true"><path d="M4.5 2.5l3 0.5 1.2 3.6-1.9 1.5a10 10 0 0 0 5.1 5.1l1.5-1.9 3.6 1.2.5 3-2 1.8C8.4 17 3 11.6 2.7 4.5z"/></svg>
      </div>
      <div class="block contact-phone">
        <span class="accent">(+65)</span> 8043 5617
      </div>

      <div class="icon-box">
        <svg viewBox="0 0 20 20" aria-hidden="true"><path d="M2 5h16v10H2z M2 5l8 6 8-6" fill="none" stroke="#e0262b" stroke-width="2"/></svg>
      </div>
      <div class="block contact-email">
        marcus<span class="accent">@kestreloak.com.sg</span>
      </div>
    </div>
  </section>

  <section class="card card-back">
    <div class="wordmark">KestrelOak</div>
  </section>

</body>
</html>
```